Business Card Design for Flood Rescue 360 - Property Restoration Professionals

I need a business card designed for Flood Rescue 360. We are a full-service property restoration solution. Providing water, fire, smoke & storm restoration as well as mold remediation and full remodel or reconstruction to homes and businesses across Dallas-Fort Worth, TX.
Target Market(s)
home and business owners with insurance covered property damage from water, fire or storm related damage
Industry/Entity Type
property restoration
Contact Information for Business Card
Marcus Pelley General Manager Cell: 214-555-0193 Office: 469-555-0148 email: Marcus@FloodRescue360.example services: Water, Fire, Mold, Reconstruction Tagline: Urgency for Your Water Emergency!
Look and feel
Each slider illustrates characteristics of the customer's brand and the style your logo design should communicate.

```html
<!DOCTYPE html>
<html lang="en">
<head>
<meta charset="utf-8">
<title>Flood Rescue 360 – Business Card</title>
<link rel="stylesheet" href="https://fonts.googleapis.com/css2?family=Montserrat:wght@400;500;700;800;900&display=swap">
<style>
  :root {
    --brand-blue: #00b2e6;
    --deep-blue: #0b6f95;
    --ink: #1d1d1f;
    --paper: #ffffff;
    --backdrop: #ecebe9;
  }
  * { box-sizing: border-box; margin: 0; padding: 0; }
  html, body {
    width: 1200px; height: 768px; overflow: hidden;
    background: var(--backdrop);
    font-family: "Montserrat", sans-serif;
  }
  .sheet {
    width: 1200px; height: 768px;
    display: flex; align-items: center; justify-content: center; gap: 40px;
  }
  .card {
    position: relative;
    width: 520px; height: 297px;
    overflow: hidden;
    box-shadow: 0 10px 28px rgba(0,0,0,0.14);
  }

  /* Front */
  .card--front { background: var(--paper); }
  .brand-name {
    position: absolute; left: 34px; top: 30px;
    display: flex; align-items: center; gap: 14px;
  }
  .brand-name__text {
    font-weight: 900; font-size: 40px; line-height: 0.95;
    text-transform: uppercase; letter-spacing: -0.5px;
    color: var(--brand-blue);
  }
  .brand-name__dot {
    width: 58px; height: 58px; border-radius: 50%;
    background: var(--brand-blue);
  }
  .person {
    position: absolute; left: 34px; top: 150px;
  }
  .person__name { font-weight: 800; font-size: 19px; color: var(--brand-blue); }
  .person__title { font-weight: 500; font-size: 12px; color: var(--ink); margin-top: 2px; }
  .divider {
    position: absolute; left: 214px; top: 150px;
    width: 2px; height: 62px; background: var(--brand-blue);
  }
  .contacts {
    position: absolute; left: 230px; top: 148px;
    list-style: none; display: flex; flex-direction: column; gap: 6px;
  }
  .contacts__item {
    display: flex; align-items: center; gap: 8px;
    font-size: 12.5px; font-weight: 500; color: var(--ink);
  }
  .contacts__icon { width: 13px; height: 13px; flex: none; }
  .service-band {
    position: absolute; left: 0; right: 0; bottom: 24px; height: 34px;
    background: var(--brand-blue);
    display: flex; align-items: center; padding-left: 34px;
    color: var(--paper); font-weight: 600; font-size: 13px; letter-spacing: 0.3px;
  }

  /* Back */
  .card--back {
    background: var(--brand-blue);
    display: flex; flex-direction: column; align-items: center; justify-content: center;
    gap: 26px;
  }
  .card--back .brand-name { position: static; }
  .card--back .brand-name__text { color: var(--deep-blue); font-size: 44px; }
  .card--back .brand-name__dot { background: var(--deep-blue); width: 62px; height: 62px; }
  .tagline {
    color: var(--paper); font-weight: 800; font-size: 14px; letter-spacing: 0.3px;
  }
</style>
</head>
<body>
<main class="sheet">
  <section class="card card--front" aria-label="Card front">
    <div class="brand-name">
      <div class="brand-name__text">Flood<br>Rescue 360</div>
      <span class="brand-name__dot"></span>
    </div>

    <div class="person">
      <p class="person__name">Marcus Pelley</p>
      <p class="person__title">General Manager</p>
    </div>
    <span class="divider"></span>
    <ul class="contacts">
      <li class="contacts__item">
        <svg class="contacts__icon" viewBox="0 0 24 24" aria-hidden="true"><path fill="#00b2e6" d="M6.6 10.8a15.1 15.1 0 0 0 6.6 6.6l2.2-2.2c.3-.3.7-.4 1-.2 1.1.4 2.3.6 3.6.6.6 0 1 .4 1 1V20c0 .6-.4 1-1 1A17 17 0 0 1 3 4c0-.6.4-1 1-1h3.5c.6 0 1 .4 1 1 0 1.3.2 2.5.6 3.6.1.3 0 .7-.2 1z"/></svg>
        214-555-0193
      </li>
      <li class="contacts__item">
        <svg class="contacts__icon" viewBox="0 0 24 24" aria-hidden="true"><path fill="#00b2e6" d="M3 8c0-2 4-4 9-4s9 2 9 4v2h-5V8H8v2H3zm3 4h12l2 8H4zm6 2a2 2 0 1 0 0 4 2 2 0 0 0 0-4z"/></svg>
        469-555-0148
      </li>
      <li class="contacts__item">
        <svg class="contacts__icon" viewBox="0 0 24 24" aria-hidden="true"><path fill="#00b2e6" d="M2 5h20v14H2zm2 2v.5l8 5 8-5V7z"/></svg>
        Marcus@FloodRescue360.example
      </li>
    </ul>

    <div class="service-band">• Water • Fire • Mold • Reconstruction</div>
  </section>

  <section class="card card--back" aria-label="Card back">
    <div class="brand-name">
      <div class="brand-name__text">Flood<br>Rescue 360</div>
      <span class="brand-name__dot"></span>
    </div>
    <p class="tagline">Urgency for Your Water Emergency!</p>
  </section>
</main>
</body>
</html>
```